Business Card Design - VNT (company name)

Over 20 years of progressive technology design, migration and management experience that drives business objectives and streamlines operations. Continuously challenge conventions to meet and exceed business security, availability and functionality requirements. Maintain exceptional vendor relationships to ensure ongoing knowledge of emerging products and to secure preferred service agreements. Recruit and utilize top talent and foster a collegial environment that advances innovation and performance excellence. design logo using 3 arrows of different colors green, gold, blue

Industry/Entity Type

Progressive

Contact Information for Business Card

Martin K. Osgood
IT Strategist / Consultant

541.583.2907 MOsgood@vntosgood.example 4817 Brenning Court Alder Falls, OR 97402

Colors
0255a3
f37122
fece3e

Requirements
Must have
• Note NEW EMAIL ADDRESS
• MOsgood@vntosgood.example
• NOTE NEW ORDER of the work I do.
• Vision – Networks – Technology
Nice to have
• main color should be orange

```html
<!DOCTYPE html>
<html lang="en">
<head>
<meta charset="utf-8">
<title>VNT Business Card</title>
<link rel="stylesheet" href="https://fonts.googleapis.com/css2?family=Michroma&family=Open+Sans:wght@400;600;700&display=swap">
<style>
  :root {
    --orange: #f37122;
    --orange-deep: #e0561a;
    --orange-light: #f6883a;
    --gold: #fece3e;
    --blue: #0255a3;
    --grey-text: #4a4a4a;
    --white: #ffffff;
    --stage: #ecebe8;
  }
  * { box-sizing: border-box; margin: 0; padding: 0; }
  html, body {
    width: 1200px; height: 784px; overflow: hidden;
    background: var(--stage);
  }
  .stage {
    width: 1200px; height: 784px;
    display: flex; align-items: center; justify-content: center; gap: 40px;
  }
  .card {
    position: relative;
    width: 540px; height: 309px;
    border-radius: 4px;
    overflow: hidden;
    box-shadow: 0 6px 18px rgba(0,0,0,0.18);
  }

  /* Front */
  .card--front { background: var(--orange); }
  .card--front .pattern {
    position: absolute; inset: 0;
    background: radial-gradient(ellipse at 80% 20%, var(--orange-light) 0%, var(--orange) 45%, var(--orange-deep) 100%);
  }
  .brand {
    position: absolute; left: 0; right: 0;
    display: flex; flex-direction: column; align-items: center;
  }
  .card--front .brand { top: 104px; color: var(--white); }
  .brand-name {
    font-family: "Open Sans", sans-serif;
    font-weight: 700;
    font-size: 58px; line-height: 1; letter-spacing: 1px;
  }
  .tagline {
    font-family: "Michroma", sans-serif;
    font-size: 9.5px; letter-spacing: 1.6px; text-transform: uppercase;
    margin-top: 10px;
  }

  /* Back */
  .card--back { background: var(--white); }
  .card--back .brand { top: 36px; }
  .card--back .brand-name { color: var(--orange); }
  .service-band {
    position: absolute; left: 0; right: 0; top: 118px;
    height: 20px; background: var(--orange);
    display: flex; align-items: center; justify-content: center;
  }
  .service-band .tagline { color: var(--white); margin: 0; font-size: 10px; letter-spacing: 2.4px; }
  .contact {
    position: absolute; left: 0; right: 0; top: 150px;
    text-align: center; color: var(--grey-text);
    font-family: "Open Sans", sans-serif;
  }
  .contact-name {
    font-family: "Michroma", sans-serif;
    color: var(--orange); font-size: 19px; letter-spacing: 1px; text-transform: uppercase;
  }
  .contact-role {
    font-family: "Michroma", sans-serif;
    font-size: 7.5px; letter-spacing: 1.4px; text-transform: uppercase; margin-top: 2px;
  }
  .contact-phone {
    color: var(--orange); font-weight: 600; font-size: 20px; margin-top: 8px;
  }
  .contact-email { font-size: 14px; margin-top: 2px; }
  .contact-address { font-size: 15px; font-weight: 600; margin-top: 2px; }
</style>
</head>
<body>
  <main class="stage">
    <section class="card card--front">
      <div class="pattern" role="img" aria-label="Decorative pattern of soft orange circles"></div>
      <div class="brand">
        <span class="brand-name">VNT</span>
        <p class="tagline">Vision – Networks – Technology</p>
      </div>
    </section>

    <section class="card card--back">
      <div class="brand">
        <span class="brand-name">VNT</span>
      </div>
      <div class="service-band">
        <p class="tagline">Vision – Networks – Technology</p>
      </div>
      <div class="contact">
        <p class="contact-name">Martin K. Osgood</p>
        <p class="contact-role">IT Strategist / Consultant</p>
        <p class="contact-phone">541.583.2907</p>
        <p class="contact-email">MOsgood@vntosgood.example</p>
        <p class="contact-address">4817 Brenning Court Alder Falls, OR 97402</p>
      </div>
    </section>
  </main>
</body>
</html>
```